Website for software company "velora"

We need a website for our software company/startup named "velora". We are developing several products (currently 3 standard-software products) which are all in different sectors, but all our products are available for Laptops/PC/Mobile Phones/Tablets, ... We do also create custom software and support our customers with consulting to optimize their processes.
We already have a Logo which you can find in the attached files.
We are a young team of 4 members (two founders and 2 employees).

To get an idea of our products -> the first one is a planning software for healthcare organizations (eg. BlueHaven, firebrigade, pharmacy), the second one is a booking software for sport clubs and the third one is a competition software for sports hunting. You see very diverse. Include or ignore this info of our products as you like.

The design has to be a bootstrap 4 (or higher) design. We have licenced FontAwesome as iconset. Responsive design should come without saying.

• Starting page, product pages, news section, contact, team, services

```html
<!DOCTYPE html>
<html lang="en">
<head>
<meta charset="utf-8">
<title>velora – Software for every sector</title>
<link rel="stylesheet" href="https://fonts.googleapis.com/css2?family=Montserrat:wght@600;700;800&family=Roboto:wght@400;500;700&display=swap">
<style>
:root{
  --orange:#f26b21;
  --navy:#1c2533;
  --ink:#1a1a1a;
  --text:#555b66;
  --peach:#fbeee3;
  --white:#ffffff;
}
*{box-sizing:border-box;margin:0;padding:0}
html,body{width:1200px;height:4886px;overflow:hidden}
body{position:relative;background:var(--white);font-family:"Roboto",Arial,sans-serif;color:var(--text)}
.abs{position:absolute}
h1,h2,h3,.logo{font-family:"Montserrat",Arial,sans-serif}
.accent{color:var(--orange)}
.btn{position:absolute;display:flex;align-items:center;justify-content:center;gap:8px;background:var(--orange);color:var(--white);font:700 15px "Roboto",Arial,sans-serif;border-radius:24px;text-transform:uppercase;letter-spacing:.2px}
.btn svg{width:15px;height:15px}
.photo{position:absolute;overflow:hidden}

/* header & hero */
.logo{font-weight:800;letter-spacing:1px}
.site-logo{left:110px;top:22px;font-size:42px;color:var(--navy)}
.nav{top:40px;font:500 14px "Roboto",Arial,sans-serif;color:var(--white)}
.hero-photo{left:770px;top:100px;width:380px;height:560px;border-radius:8px;background:linear-gradient(160deg,#3a4a60 0%,#d7dde6 45%,#5b6b80 100%)}
.hero-title{left:110px;top:300px;font-size:45px;line-height:54px;font-weight:700;color:var(--ink)}
.hero-text{left:110px;top:492px;width:500px;font-size:16px;line-height:28px;color:#222}

/* products */
.section-title{left:0;width:1200px;text-align:center;font-size:48px;font-weight:700;color:var(--ink)}
.circle-photo{border-radius:50%}
.product-title{font-size:46px;line-height:50px;font-weight:700;color:var(--ink)}
.product-text{width:340px;font-size:14.5px;line-height:25px;color:var(--text)}
.product-text p+p{margin-top:10px}
.dash-shot{position:absolute;width:496px;height:309px;border-radius:10px;background:linear-gradient(90deg,#1c2533 0%,#1c2533 21%,#eef1f5 21%,#dfe4ea 100%);box-shadow:0 30px 50px rgba(20,30,45,.18)}

/* features */
.feature-title{font:700 16px "Roboto",Arial,sans-serif;color:var(--white)}
.feature-text{margin-top:10px;width:195px;font-size:13.5px;line-height:19px;color:#e3e6ea}
.feature-icon{position:absolute;width:66px;height:66px;border-radius:50%;background:var(--orange);display:flex;align-items:center;justify-content:center}
.feature-icon svg{width:34px;height:34px}
.mark{font-size:120px;font-weight:800;color:var(--orange);left:0;width:1200px;text-align:center}

/* reviews */
.review{position:absolute;width:408px;height:228px;background:var(--white);border-radius:24px;box-shadow:0 14px 28px rgba(0,0,0,.12)}
.review .quote{position:absolute;left:98px;top:20px;font:800 54px "Montserrat",Arial,sans-serif;color:var(--orange);line-height:1}
.review p{position:absolute;left:100px;top:76px;width:288px;font-size:13.5px;line-height:24px;color:#8a8f97}
.review h3{position:absolute;left:100px;top:160px;font:700 16px "Roboto",Arial,sans-serif;color:#111}
.review .stars{position:absolute;left:100px;top:182px;display:flex;gap:3px}
.avatar-ph{position:absolute;width:114px;height:114px;border-radius:50%;border:4px solid var(--white);box-shadow:0 6px 16px rgba(0,0,0,.15);background:linear-gradient(160deg,#8a6e5a,#d9c8b8 60%,#4b5564)}
.arrow{position:absolute;width:26px;height:40px}

/* resources */
.card{position:absolute;top:3940px;width:311px;height:388px;background:var(--white);box-shadow:0 6px 22px rgba(0,0,0,.09)}
.card .photo{left:9px;top:10px;width:293px;height:202px;background:linear-gradient(150deg,#1e2633,#4a5a72 55%,#a8b4c4)}
.card .date{position:absolute;top:232px;width:100%;text-align:center;font-size:13.5px;color:var(--orange)}
.card h3{position:absolute;top:256px;width:100%;text-align:center;font:700 16px "Roboto",Arial,sans-serif;color:#111}
.card p{position:absolute;top:288px;left:20px;right:20px;text-align:center;font-size:13.5px;line-height:23px;color:#777}
.card .more{position:absolute;top:348px;width:100%;text-align:center;font:700 14px "Roboto",Arial,sans-serif;color:var(--orange)}

/* footer */
.foot-h{font:700 15px "Roboto",Arial,sans-serif;color:var(--white)}
.foot-txt{font-size:13px;line-height:19px;color:#e4e7eb}
.foot-links{list-style:none;font-size:13px;line-height:26px;color:#e4e7eb}
.contact-row{position:absolute;display:flex;gap:12px}
.contact-row svg{width:12px;height:12px;margin-top:3px;flex:none}
.contact-row b{display:block;font-size:12px;color:var(--white)}
.subscribe{left:787px;top:4640px;width:300px;height:44px;background:var(--white);border-radius:22px}
.subscribe span{position:absolute;left:28px;top:14px;font-size:12px;color:#999}
.subscribe .go{position:absolute;right:0;top:0;width:122px;height:44px;border-radius:22px;background:var(--orange);color:var(--white);font:700 15px "Roboto",Arial,sans-serif;display:flex;align-items:center;justify-content:center}
.social{position:absolute;top:4750px;width:32px;height:32px;border-radius:50%;border:1.5px solid var(--white)}
.bottom{top:4838px;font-size:12.5px;color:#e4e7eb}
</style>
</head>
<body>

<svg width="0" height="0" style="position:absolute">
  <defs>
    <symbol id="arrow-circle" viewBox="0 0 16 16"><circle cx="8" cy="8" r="8" fill="#fff"/><path d="M6.5 4.5 10 8l-3.5 3.5" fill="none" stroke="#f26b21" stroke-width="2"/></symbol>
    <symbol id="arrow-circle-o" viewBox="0 0 16 16"><circle cx="8" cy="8" r="7" fill="none" stroke="#f26b21" stroke-width="2"/><path d="M6.5 5 9.5 8l-3 3" fill="none" stroke="#f26b21" stroke-width="2"/></symbol>
    <symbol id="star" viewBox="0 0 20 20"><path d="M10 1l2.7 5.9 6.3.6-4.8 4.3 1.4 6.3L10 14.8 4.4 18.1l1.4-6.3L1 7.5l6.3-.6z" fill="#f26b21"/></symbol>
    <symbol id="calendar" viewBox="0 0 16 16"><rect x="1" y="3" width="14" height="12" rx="1" fill="#f26b21"/><rect x="3" y="7" width="10" height="6" fill="#fff"/><rect x="4" y="1" width="2" height="4" fill="#f26b21"/><rect x="10" y="1" width="2" height="4" fill="#f26b21"/></symbol>
  </defs>
</svg>

<!-- header / hero -->
<svg class="abs" style="left:0;top:0" width="1200" height="720" viewBox="0 0 1200 720" aria-hidden="true">
  <polygon points="330,0 1200,0 1200,568 1052,716 700,360" fill="#1c2533"/>
</svg>
<div class="abs logo site-logo">velora</div>
<nav>
  <span class="abs nav" style="left:444px">Home</span>
  <span class="abs nav" style="left:517px">Our Products</span>
  <span class="abs nav" style="left:638px">Our Features</span>
  <span class="abs nav" style="left:758px">Testimonials</span>
  <span class="abs nav" style="left:876px">Team</span>
  <span class="abs nav" style="left:946px">News</span>
  <span class="abs nav" style="left:1016px">ContactUs</span>
</nav>
<div class="photo hero-photo" role="img" aria-label="Smiling young man in a light blue shirt holding an open laptop"></div>

<h1 class="abs hero-title"><span class="accent">Developing several</span><br>Products by experienced<br>entrepreneurs</h1>
<p class="abs hero-text">Lorem ipsum dolor sit amet, consectetur adipiscing elit, sed do incididunt ut labore et dolore magna aliqua.</p>
<a class="btn" style="left:110px;top:582px;width:208px;height:48px">Get Started <svg><use href="#arrow-circle"/></svg></a>

<!-- products -->
<h2 class="abs section-title" style="top:772px"><span class="accent">Our</span> Products</h2>

<div class="photo circle-photo" style="left:89px;top:872px;width:346px;height:346px;background:linear-gradient(150deg,#e9eef3,#b7c6d6 50%,#2f6fb8)" role="img" aria-label="Team of doctors and nurses reviewing a clipboard"></div>
<div class="dash-shot" style="left:171px;top:1094px" role="img" aria-label="Screenshot of the healthcare planning dashboard"></div>
<h2 class="abs product-title" style="left:740px;top:970px">Healthcare<br>Organizations</h2>
<div class="abs product-text" style="left:749px;top:1098px"><p>Lorem ipsum dolor sit amet, consectetur adipiscing elit, sed do eiusmod tempor incididunt ut labore et dolore magna aliqua.</p><p>Ut enim ad minim veniam, quis nostrud exercitation ullamco laboris nisi ut aliquip ex ea commodo aute irure dolor in reprehenderit in consequat.</p></div>
<a class="btn" style="left:749px;top:1289px;width:172px;height:46px">Learn More <svg><use href="#arrow-circle"/></svg></a>

<h2 class="abs product-title" style="left:110px;top:1592px">Sport Clubs</h2>
<div class="abs product-text" style="left:116px;top:1676px"><p>Lorem ipsum dolor sit amet, consectetur adipiscing elit, sed do eiusmod tempor incididunt ut labore et dolore magna aliqua.</p><p>Ut enim ad minim veniam, quis nostrud exercitation ullamco laboris nisi ut aliquip ex ea commodo aute irure dolor in reprehenderit in consequat.</p></div>
<a class="btn" style="left:116px;top:1867px;width:172px;height:46px">Learn More <svg><use href="#arrow-circle"/></svg></a>
<div class="photo circle-photo" style="left:760px;top:1469px;width:350px;height:350px;background:linear-gradient(180deg,#cfe0ee 0%,#a9b8c4 45%,#6d9a4f 75%,#4f7d3a 100%)" role="img" aria-label="Boy in a blue jersey kicking a football on a field"></div>
<div class="dash-shot" style="left:537px;top:1688px" role="img" aria-label="Screenshot of the sport club booking dashboard"></div>

<div class="photo circle-photo" style="left:89px;top:2066px;width:346px;height:346px;background:linear-gradient(140deg,#6b4a2a,#b07a3e 45%,#2c2a26 80%)" role="img" aria-label="Hunting rifle with scope resting on autumn leaves"></div>
<div class="dash-shot" style="left:171px;top:2284px" role="img" aria-label="Screenshot of the sports hunting competition dashboard"></div>
<h2 class="abs product-title" style="left:740px;top:2186px">Sports Hunting</h2>
<div class="abs product-text" style="left:749px;top:2277px"><p>Lorem ipsum dolor sit amet, consectetur adipiscing elit, sed do eiusmod tempor incididunt ut labore et dolore magna aliqua.</p><p>Ut enim ad minim veniam, quis nostrud exercitation ullamco laboris nisi ut aliquip ex ea commodo aute irure dolor in reprehenderit in consequat.</p></div>
<a class="btn" style="left:749px;top:2468px;width:172px;height:46px">Learn More <svg><use href="#arrow-circle"/></svg></a>

<!-- features -->
<svg class="abs" style="left:0;top:2749px" width="1200" height="528" viewBox="0 0 1200 528" aria-hidden="true">
  <polygon points="0,165 600,0 1200,165 1200,527 0,527" fill="#f26b21"/>
  <polygon points="0,208 600,46 1200,208 1200,527 0,527" fill="#1c2533"/>
</svg>
<h2 class="abs section-title" style="top:2858px;color:var(--white)"><span class="accent">Our</span> Features</h2>
<div class="abs logo mark" style="top:2990px">velora</div>

<div class="abs" style="left:112px;top:2962px;text-align:right">
  <div class="feature-title">Lorem ipsum sit amet</div>
  <div class="feature-text">Sed ut perspiciatis unde omnis iste natus error sit voluptatem accusantium doloremque</div>
</div>
<div class="feature-icon" style="left:329px;top:2968px"><svg viewBox="0 0 34 34" fill="none" stroke="#fff" stroke-width="1.6"><rect x="4" y="6" width="22" height="18" rx="2"/><path d="M4 11h22M12 16l-3 3 3 3M18 16l3 3-3 3"/><circle cx="26" cy="26" r="5"/></svg></div>
<div class="abs" style="left:112px;top:3100px;text-align:right">
  <div class="feature-title">Lorem ipsum sit amet</div>
  <div class="feature-text">Sed ut perspiciatis unde omnis iste natus error sit voluptatem accusantium doloremque</div>
</div>
<div class="feature-icon" style="left:329px;top:3106px"><svg viewBox="0 0 34 34" fill="none" stroke="#fff" stroke-width="1.6"><circle cx="17" cy="17" r="12"/><path d="M11 17a6 6 0 0 1 12 0M17 5v4M17 25v4M5 17h4M25 17h4"/></svg></div>

<div class="feature-icon" style="left:801px;top:2968px"><svg viewBox="0 0 34 34" fill="none" stroke="#fff" stroke-width="1.6"><rect x="9" y="3" width="16" height="28" rx="2"/><path d="M14 27h6M13 12h8M13 16h8M13 20h5"/></svg></div>
<div class="abs" style="left:893px;top:2962px">
  <div class="feature-title">Lorem ipsum sit amet</div>
  <div class="feature-text">Sed ut perspiciatis unde omnis iste natus error sit voluptatem accusantium doloremque</div>
</div>
<div class="feature-icon" style="left:801px;top:3106px"><svg viewBox="0 0 34 34" fill="none" stroke="#fff" stroke-width="1.6"><rect x="4" y="6" width="26" height="18" rx="2"/><path d="M13 29h8M17 24v5M9 18l5-5 4 3 6-6"/></svg></div>
<div class="abs" style="left:893px;top:3100px">
  <div class="feature-title">Lorem ipsum sit amet</div>
  <div class="feature-text">Sed ut perspiciatis unde omnis iste natus error sit voluptatem accusantium doloremque</div>
</div>

<!-- reviews -->
<div class="abs" style="left:0;top:3276px;width:1200px;height:494px;background:var(--peach)"></div>
<h2 class="abs section-title" style="top:3350px">Customer <span class="accent">Reviews</span></h2>
<svg class="arrow" style="left:36px;top:3539px" viewBox="0 0 26 40"><path d="M20 4 6 20l14 16" fill="none" stroke="#1c2533" stroke-width="4"/></svg>
<svg class="arrow" style="left:1134px;top:3539px" viewBox="0 0 26 40"><path d="M6 4l14 16L6 36" fill="none" stroke="#1c2533" stroke-width="4"/></svg>

<div class="review" style="left:167px;top:3445px">
  <div class="quote">&ldquo;</div>
  <p>Sed ut perspiciatis unde omnis iste natus error sit voluptatem accusantium doloremque laudantium, totam rem aperiam,</p>
  <h3>Marek Lindholm</h3>
  <div class="stars"><svg width="15" height="15"><use href="#star"/></svg><svg width="15" height="15"><use href="#star"/></svg><svg width="15" height="15"><use href="#star"/></svg><svg width="15" height="15"><use href="#star"/></svg><svg width="15" height="15"><use href="#star"/></svg></div>
</div>
<div class="avatar-ph" style="left:116px;top:3502px" role="img" aria-label="Portrait of a smiling customer with glasses"></div>

<div class="review" style="left:677px;top:3445px">
  <div class="quote">&ldquo;</div>
  <p>Sed ut perspiciatis unde omnis iste natus error sit voluptatem accusantium doloremque laudantium, totam rem aperiam,</p>
  <h3>Priya Osei</h3>
  <div class="stars"><svg width="15" height="15"><use href="#star"/></svg><svg width="15" height="15"><use href="#star"/></svg><svg width="15" height="15"><use href="#star"/></svg><svg width="15" height="15"><use href="#star"/></svg><svg width="15" height="15"><use href="#star"/></svg></div>
</div>
<div class="avatar-ph" style="left:626px;top:3502px;background:linear-gradient(160deg,#2a3448,#9aa6b8 60%,#3b4658)" role="img" aria-label="Portrait of a customer in a dark suit"></div>

<!-- resources -->
<h2 class="abs section-title" style="top:3850px;text-transform:uppercase"><span class="accent">Our</span> Resources</h2>

<article class="card" style="left:110px">
  <div class="photo" role="img" aria-label="Smiling developer at a desk with several monitors"></div>
  <div class="date"><svg width="12" height="12" style="vertical-align:-1px"><use href="#calendar"/></svg> January 12, 2020</div>
  <h3>Lorem ipsum dolor sit amet</h3>
  <p>Sed ut perspiciatis unde omnis iste natus error sit voluptatem accusantium</p>
  <div class="more">READ MORE <svg width="13" height="13" style="vertical-align:-2px"><use href="#arrow-circle-o"/></svg></div>
</article>
<article class="card" style="left:446px">
  <div class="photo" style="background:linear-gradient(150deg,#0f1a2c,#2f4a74 55%,#7fa0c8)" role="img" aria-label="Team working in a dark office with glowing screens"></div>
  <div class="date"><svg width="12" height="12" style="vertical-align:-1px"><use href="#calendar"/></svg> January 12, 2020</div>
  <h3>Lorem ipsum dolor sit amet</h3>
  <p>Sed ut perspiciatis unde omnis iste natus error sit voluptatem accusantium</p>
  <div class="more">READ MORE <svg width="13" height="13" style="vertical-align:-2px"><use href="#arrow-circle-o"/></svg></div>
</article>
<article class="card" style="left:779px">
  <div class="photo" style="background:linear-gradient(150deg,#2a2f3a,#6c7788 55%,#c4ccd6)" role="img" aria-label="Programmer typing code on a laptop at a desk"></div>
  <div class="date"><svg width="12" height="12" style="vertical-align:-1px"><use href="#calendar"/></svg> January 12, 2020</div>
  <h3>Lorem ipsum dolor sit amet</h3>
  <p>Sed ut perspiciatis unde omnis iste natus error sit voluptatem accusantium</p>
  <div class="more">READ MORE <svg width="13" height="13" style="vertical-align:-2px"><use href="#arrow-circle-o"/></svg></div>
</article>

<!-- footer -->
<svg class="abs" style="left:0;top:4418px" width="1200" height="468" viewBox="0 0 1200 468" aria-hidden="true">
  <polygon points="0,151 600,0 1200,151 1200,468 0,468" fill="#f26b21"/>
  <polygon points="0,190 600,38 1200,190 1200,468 0,468" fill="#1c2533"/>
</svg>
<div class="abs logo" style="left:110px;top:4668px;font-size:52px;color:var(--white)">velora</div>

<div class="abs foot-h" style="left:402px;top:4590px">Our Office Address</div>
<div class="contact-row foot-txt" style="left:402px;top:4630px"><svg viewBox="0 0 12 12"><path d="M2 1h3l1 3-2 1a7 7 0 0 0 3 3l1-2 3 1v3c-6 0-9-3-9-9z" fill="#f26b21"/></svg><div><b>Phone</b>+43 5550 10472</div></div>
<div class="contact-row foot-txt" style="left:402px;top:4684px"><svg viewBox="0 0 12 12"><rect x="0" y="2" width="12" height="8" fill="#f26b21"/><path d="M0 2l6 4 6-4" fill="none" stroke="#1c2533"/></svg><div><b>Email</b>office@velora.at</div></div>
<div class="contact-row foot-txt" style="left:402px;top:4738px"><svg viewBox="0 0 12 12"><path d="M6 0a4 4 0 0 1 4 4c0 3-4 8-4 8S2 7 2 4a4 4 0 0 1 4-4z" fill="#f26b21"/><circle cx="6" cy="4" r="1.5" fill="#1c2533"/></svg><div><b>Location</b>6625 Lorem ipsum dolor amet,<br>consectetur adipiscing elit</div></div>

<div class="abs foot-h" style="left:656px;top:4590px">Company</div>
<ul class="abs foot-links" style="left:656px;top:4628px"><li>Home</li><li>Our Products</li><li>Our Features</li><li>Testimonials</li><li>Team</li><li>ContactUs</li></ul>

<div class="abs foot-h" style="left:787px;top:4590px">Subscribe for Updates</div>
<div class="abs subscribe"><span>Email Address</span><div class="go">SUBMIT</div></div>
<div class="abs foot-txt" style="left:787px;top:4708px;display:flex;gap:8px;align-items:center"><svg width="12" height="12" viewBox="0 0 12 12"><rect x=".5" y=".5" width="11" height="11" fill="none" stroke="#fff"/><path d="M3 6l2 2 4-4" fill="none" stroke="#fff" stroke-width="1.5"/></svg>Yes, Please Contact me.</div>
<div class="social" style="left:787px"></div>
<div class="social" style="left:829px"></div>
<div class="social" style="left:871px"></div>

<div class="abs foot-txt" style="left:1020px;top:4796px;font-size:11px;font-weight:700"><svg width="10" height="10" viewBox="0 0 10 10" style="vertical-align:-1px"><path d="M5 1 1 5h2.5v4h3V5H9z" fill="#fff"/></svg> Go Up</div>

<div class="abs bottom" style="left:110px">© 2022 velora | All Rights Reserved</div>
<div class="abs bottom" style="left:760px">Privacy Policy &nbsp;|&nbsp; Cookie Policy &nbsp;|&nbsp; Terms Of Services</div>

</body>
</html>
```